Communication and Marketing agency needs a new presentation card

We are a group of communication and marketing agencies specialized in companies that are in the logistics and industrial sector. The head agency is TELVANO Grupo and the group consists of 4 agencies: TELVANO Media, TELVANO Digital, TELVANO Research and DifundeEnPantalla. We hace 4 offices in Spain (Madrid, Barcelona, Valencia and Murcia). We are looking for a clean and attractive design that transmits our experience, brand presence in the market and knowledge to those who receive the card.It has to maintain the colors of the logo that is attached.
Target Market(s)
logistics and industrial sector
Marketing department
Contact Information for Business Card
Clean and attractive design

```html
<!DOCTYPE html>
<html lang="en">
<head>
<meta charset="utf-8">
<title>TELVANO Business Card</title>
<link href="https://fonts.googleapis.com/css2?family=Open+Sans:wght@400;600;700&display=swap" rel="stylesheet">
<style>
  :root {
    --backdrop: #c98084;
    --card: #ffffff;
    --brand-red: #b31b24;
    --brand-grey: #58595b;
    --ink: #2b2b2b;
  }
  * { box-sizing: border-box; margin: 0; padding: 0; }
  html, body { width: 1200px; height: 1200px; overflow: hidden; }
  body {
    background: var(--backdrop);
    font-family: "Open Sans", Arial, sans-serif;
    position: relative;
  }
  .card {
    position: absolute;
    left: 224px;
    width: 814px;
    height: 465px;
    background: var(--card);
    border-radius: 26px;
  }
  .card--front { top: 76px; }
  .card--back { top: 658px; }

  .wordmark {
    position: absolute;
    text-align: right;
    font-weight: 600;
    line-height: 1;
  }
  .wordmark__name { display: block; letter-spacing: 4px; }
  .wordmark__division { display: block; }

  .card--front .wordmark {
    right: 152px;
    top: 150px;
    color: var(--brand-grey);
  }
  .card--front .wordmark__name { font-size: 100px; }
  .card--front .wordmark__division { font-size: 60px; margin-top: 2px; }

  .card--back .wordmark {
    right: 47px;
    top: 54px;
    color: var(--brand-red);
  }
  .card--back .wordmark__name { font-size: 86px; }
  .card--back .wordmark__division { font-size: 52px; margin-top: 2px; }

  .holder {
    position: absolute;
    left: 53px;
    top: 262px;
  }
  .holder__name {
    color: var(--brand-red);
    font-weight: 700;
    font-size: 25px;
    line-height: 1.2;
  }
  .holder__role {
    color: var(--ink);
    font-size: 18px;
    margin-top: 4px;
  }
  .divider {
    position: absolute;
    left: 53px;
    right: 47px;
    top: 326px;
    height: 1px;
    background: var(--brand-red);
  }
  .divider::before {
    content: "";
    position: absolute;
    left: 0;
    top: -1px;
    width: 214px;
    height: 3px;
    background: var(--brand-red);
  }
  .contacts {
    position: absolute;
    left: 53px;
    top: 346px;
    list-style: none;
    font-size: 18.5px;
    color: var(--ink);
  }
  .contacts li {
    display: flex;
    align-items: center;
    height: 24px;
  }
  .contacts svg { width: 15px; height: 15px; margin-right: 8px; flex: none; }
  .address {
    position: absolute;
    right: 47px;
    top: 370px;
    text-align: right;
    font-size: 18.5px;
    line-height: 24px;
    color: var(--ink);
    font-style: normal;
  }
</style>
</head>
<body>
  <section class="card card--front">
    <div class="wordmark">
      <span class="wordmark__name">TELVANO</span>
      <span class="wordmark__division">Digital</span>
    </div>
  </section>

  <section class="card card--back">
    <div class="wordmark">
      <span class="wordmark__name">TELVANO</span>
      <span class="wordmark__division">Grupo</span>
    </div>

    <div class="holder">
      <div class="holder__name">Marco Ellison</div>
      <div class="holder__role">Manager</div>
    </div>
    <div class="divider"></div>

    <ul class="contacts">
      <li>
        <svg viewBox="0 0 16 16" aria-hidden="true"><path d="M4 1.5l2.2 3-1.3 1.4c.8 1.8 2.2 3.3 4 4.3l1.4-1.3 3 2.1-1.2 2.6C7 13.3 2.5 8.6 1.8 2.8z" fill="var(--brand-red)"/></svg>
        +555 -214- 0386
      </li>
      <li>
        <svg viewBox="0 0 16 16" aria-hidden="true"><rect x="1" y="3" width="14" height="10" fill="var(--brand-red)"/><path d="M1 3l7 6 7-6M1 13l5-5M15 13l-5-5" stroke="#fff" stroke-width="1.2" fill="none"/></svg>
        info@brasswell.ca
      </li>
      <li>
        <svg viewBox="0 0 16 16" aria-hidden="true"><circle cx="8" cy="8" r="6.5" fill="none" stroke="var(--brand-red)" stroke-width="1.3"/><ellipse cx="8" cy="8" rx="3" ry="6.5" fill="none" stroke="var(--brand-red)" stroke-width="1"/><path d="M1.5 8h13M2.5 5h11M2.5 11h11" stroke="var(--brand-red)" stroke-width="1"/></svg>
        www.brasswell.ca
      </li>
    </ul>

    <address class="address">
      #210 – 4870 57TH Avenue NW<br>
      Calgary AB T2P 0X0 CANADA
    </address>
  </section>
</body>
</html>
```